Luxury Tours Design

We are “Amber Coachline” a Chauffeur Company based in Maidenhead, Berkshire. Our website is - ambercoachline.co.uk which will give you an insite into the Company.
Our clients consist of luxurious Hotels, large Corporate Companies along with private UHNW clients.
We have a fleet of Valtrane E, S and V Class vehicles along with 16 Seater Executive Coaches so we can accommodate single travellers, couples, friends, families and groups.
We would like an A5 (or slightly larger) double sided colour leaflet designed to promote our Tours in our local and surrounding areas.
The information below is some indication as to what we would like.
On the front we would like:-
Amber Coachline “Signature Tour” This will be our main promoting Tour
Slogan “Amber Coachline….ever at your service”
Tour will include:-
Visiting the historic town of Windsor, Hollenby Castle, St Aldric’s Chapel and Regal Pemberly Shopping Arcade.
Then onto Eton (Dunmere College) and a lovely view of the River Thames along with an array of Antique Shops in the quaint streets.
Bray Village (Heron Isle), renowed for it’s Brevard Star Restaurants and pubs.
Through picturesque Cookham along to Marlow for some shopping in the boutique shops, small listed buildings and beautiful places for refreshments, along with stunning views of the River Thames form Ashcombe Bridge.
This will be our main tour we offer but again this is flexible. This aims to be around 4-5 hours.
On the front, a picture of Hollenby castle maybe a large picture with writing over the top, or a separate photo….. a couple of photos attached or something similar.
On the back of the leaflet:-
We offer London based tours including:-
Belvards, Larkmoor Park, Ravensholt Palace, Corringdale Palace, Pellington Square, Turning of the Sentries, Keep of Ardmoor, Tall Tom, Glenmoreton Abbey to name a few! Or maybe London by night with a show or restaurant.
On the back a picture of Corringdale Palace…a couple of picture are also attached or again something similar.
Other Tours provided:-
Ridgewell Court Palace, Oxford and Corvane Palace, Ashmarrow Ring and Bath, The Cotswolds, Stratford and Penlow Castle, Quillford Shopping Village.
Also bespoke Tours can be arranged. We can personalise any tour to your requirements.
Experienced friendly Chauffeur’s, no request too big or small.
Please call us on 01632 960417 or email us sales@ambercoachline.co.uk
Please can you do an initial design including the above information.
Look forward to hearing from you.
Kind regards
Please visit https://www.hartleyprivatedrives.co.uk/ to get an idea of the tours of London to go on the back.
Prices will follow to be added after design and layout has been done.
Our AC logo is available on www.ambercoachline.co.uk
We want text to be editable and also for the design to have a luxury feel.
Chauffeur

```html
<!DOCTYPE html>
<html lang="en">
<head>
<meta charset="utf-8">
<title>Amber Coachline – Tours Leaflet</title>
<link href="https://fonts.googleapis.com/css2?family=Great+Vibes&family=Poppins:ital,wght@0,400;0,500;0,600;1,400;1,700&display=swap" rel="stylesheet">
<style>
:root{
  --backdrop:#dedede;
  --ink:#4a4530;
  --dark:#2b2922;
  --panel:rgba(118,108,68,0.62);
  --gold:#cdb65c;
  --gold-deep:#8f7f3c;
  --white:#ffffff;
  --text-dark:#2a2a2a;
}
*{margin:0;padding:0;box-sizing:border-box}
html,body{width:1200px;height:3283px;overflow:hidden;background:var(--backdrop);font-family:'Poppins',sans-serif}
.canvas{position:relative;width:1200px;height:3283px}
.page{position:absolute;left:70px;width:1047px;overflow:hidden;background:var(--dark);box-shadow:0 6px 24px rgba(0,0,0,.25)}
.page--front{top:96px;height:1484px}
.page--back{top:1652px;height:1483px}
.photo{position:absolute;left:0;width:100%}
.photo--castle{top:0;height:800px;background:linear-gradient(180deg,#d9e2e8 0%,#ecc7bc 22%,#e9a996 30%,#7c8260 40%,#4d6b2e 52%,#3d5a26 68%,#2b2922 100%)}
.photo--palace{top:0;height:900px;background:linear-gradient(180deg,#cfdce8 0%,#e6d5d0 22%,#eab9a6 30%,#d8d4cc 40%,#b8b4aa 52%,#c23a2a 62%,#d9c23a 70%,#a63024 78%,#2b2922 100%)}
.abs{position:absolute}
.center{left:0;width:100%;text-align:center}
.script{font-family:'Great Vibes',cursive;font-weight:400}
.title{color:var(--ink);font-size:128px;line-height:1.1}
.title--front{font-size:140px}
.slogan{color:var(--ink);font-size:58px;line-height:1.1}
.fleet{color:var(--white);font-size:24px;line-height:30px}
.panel{position:absolute;background:var(--panel)}
.tour-heading{color:var(--gold);font-size:34px;line-height:35px;font-weight:500;text-transform:uppercase}
.price{position:absolute;background:var(--gold-deep);color:var(--white)}
.price__from{position:absolute;left:28px;top:8px;font-size:13px}
.price__value{position:absolute;left:28px;top:20px;font-size:42px;font-weight:600}
.itinerary p{color:var(--white);font-size:17px;line-height:21px;margin-bottom:20px}
.quote{color:var(--gold);font-style:italic;font-size:22px;line-height:28px}
.quote b{font-family:Georgia,serif;font-style:normal;font-size:36px;vertical-align:-6px}
.contact-label{color:var(--gold);font-size:15px;letter-spacing:3px}
.contact-row{position:absolute;left:0;width:100%;height:30px;color:var(--white);font-weight:600}
.contact-item{position:absolute;display:flex;align-items:center;gap:8px;top:0}
.contact-item svg{width:22px;height:22px}
.contact-item--phone{font-size:20px}
.contact-item--mail,.contact-item--web{font-size:16px}
.sep{position:absolute;top:4px;width:1px;height:22px;background:rgba(255,255,255,.45)}
.brand{position:absolute;left:0;width:100%;display:flex;justify-content:center;align-items:center;gap:14px}
.brand__dot{width:44px;height:44px;border-radius:50%;background:#cfcac0}
.brand__name{color:var(--white);font-size:30px;font-weight:500}
.sight{position:absolute;color:var(--text-dark);font-size:22px}
.night{color:#1d1d1d;font-style:italic;font-weight:700;font-size:22px}
.other-title{color:var(--gold);font-size:70px}
.other-item{position:absolute;color:var(--white);font-size:18px;text-transform:uppercase}
.request{color:var(--gold);font-size:22px}
</style>
</head>
<body>
<div class="canvas">

  <section class="page page--front">
    <div class="photo photo--castle" role="img" aria-label="Photograph of Hollenby Castle at sunset seen down a long tree-lined avenue"></div>
    <h1 class="abs center script title title--front" style="top:28px">Signature Tour</h1>
    <p class="abs center script slogan" style="top:190px">Amber Coachline..Ever at your service..</p>
    <p class="abs center fleet" style="top:662px">We have a fleet of Valtrane E, S and V Class vehicles along with 16<br>Seater Executive Coaches so we can accommodate single travellers,<br>couples, friends, families and groups.</p>

    <div class="panel" style="left:124px;top:817px;width:801px;height:450px">
      <h2 class="abs tour-heading" style="left:31px;top:13px">Visit to the historic<br>town of Windsor</h2>
      <div class="price" style="left:540px;top:8px;width:261px;height:71px">
        <span class="price__from">FROM</span>
        <span class="price__value">£350.00</span>
      </div>
      <div class="abs itinerary" style="left:31px;top:112px;width:740px">
        <p>Visiting the historic town of Windsor, Hollenby Castle, St Aldric’s Chapel and<br>Regal Pemberly Shopping Arcade.</p>
        <p>Eton and Dunmere College with lovely views of the River Thames along with an array of<br>Antique Shops in the quaint streets.</p>
        <p>Bray Village renowned for it's Brevard Star restaurants and pubs, along with a<br>visit to Heron Isle.</p>
        <p>Through picturesque Cookham along to Marlow for some shopping in the<br>boutique shops, small listed buildings and beautiful places for refreshments,<br>along with stunning views of the River Thames from Ashcombe Bridge.</p>
      </div>
      <p class="abs center quote" style="top:384px"><b>“</b>Our signature tour is approximately 4 hours<b>”</b></p>
    </div>

    <p class="abs center contact-label" style="top:1289px">CONTACT US</p>
    <div class="contact-row" style="top:1318px">
      <span class="contact-item contact-item--phone" style="left:104px"><svg viewBox="0 0 24 24" fill="none" stroke="#cdb65c" stroke-width="1.5"><circle cx="12" cy="12" r="11"/><path d="M8 6.5l2 .2.8 2.6-1.3 1.1a7 7 0 0 0 3.9 3.9l1.1-1.3 2.6.8.2 2a2 2 0 0 1-2 1.7A10 10 0 0 1 6.5 8.5 2 2 0 0 1 8 6.5z"/></svg>01632 960417</span>
      <span class="sep" style="left:312px"></span>
      <span class="contact-item contact-item--mail" style="left:340px"><svg viewBox="0 0 24 24" fill="none" stroke="#cdb65c" stroke-width="1.5"><circle cx="12" cy="12" r="11"/><rect x="6.5" y="8" width="11" height="8" rx="1"/><path d="M6.5 8.5l5.5 4 5.5-4"/></svg>sales@ambercoachline.co.uk</span>
      <span class="sep" style="left:651px"></span>
      <span class="contact-item contact-item--web" style="left:685px"><svg viewBox="0 0 24 24" fill="none" stroke="#cdb65c" stroke-width="1.5"><circle cx="12" cy="12" r="11"/><circle cx="12" cy="12" r="6"/><path d="M6 12h12M12 6c-2.5 3-2.5 9 0 12M12 6c2.5 3 2.5 9 0 12"/></svg>www.ambercoachline.co.uk</span>
    </div>
    <div class="brand" style="top:1394px"><span class="brand__dot"></span><span class="brand__name">Amber Coachline</span></div>
  </section>

  <section class="page page--back">
    <div class="photo photo--palace" role="img" aria-label="Photograph of Corringdale Palace with its memorial statue behind beds of red and yellow tulips"></div>
    <h1 class="abs center script title" style="top:20px">London Tours</h1>

    <span class="sight" style="left:96px;top:166px">Belvards</span>
    <span class="sight" style="left:96px;top:206px">Larkmoor Park</span>
    <span class="sight" style="left:96px;top:246px">Ravensholt Palace</span>
    <span class="sight" style="left:377px;top:166px">Corringdale Palace</span>
    <span class="sight" style="left:377px;top:206px">Pellington Square</span>
    <span class="sight" style="left:377px;top:246px">Turning of the Sentries</span>
    <span class="sight" style="left:731px;top:161px">Keep of Ardmoor</span>
    <span class="sight" style="left:731px;top:201px">Tall Tom</span>
    <span class="sight" style="left:731px;top:241px">Glenmoreton Abbey</span>
    <p class="abs night" style="left:96px;top:311px">Or maybe London by night with a show or restaurant.</p>

    <div class="panel" style="left:111px;top:877px;width:846px;height:409px">
      <h2 class="abs center script other-title" style="top:18px">Other Tours Available</h2>
      <span class="other-item" style="left:81px;top:140px">Ridgewell Court Palace</span>
      <span class="other-item" style="left:81px;top:180px">Oxford and Corvane Palace</span>
      <span class="other-item" style="left:81px;top:220px">Ashmarrow Ring and Bath</span>
      <span class="other-item" style="left:470px;top:140px">The Cotswolds</span>
      <span class="other-item" style="left:470px;top:180px">Stratford and Penlow Castle</span>
      <span class="other-item" style="left:470px;top:220px">Quillford Shopping Village</span>
      <p class="abs center quote" style="top:298px;font-size:19px;line-height:25px"><b>“</b> Also bespoke tours can be arranged. We can personalize any tour to <b>”</b><br>your requirements with our friendly, experienced chauffeurs</p>
      <p class="abs center request" style="top:363px">Prices On Request</p>
    </div>

    <p class="abs center contact-label" style="top:1318px">CONTACT US</p>
    <div class="contact-row" style="top:1347px">
      <span class="contact-item contact-item--phone" style="left:104px"><svg viewBox="0 0 24 24" fill="none" stroke="#cdb65c" stroke-width="1.5"><circle cx="12" cy="12" r="11"/><path d="M8 6.5l2 .2.8 2.6-1.3 1.1a7 7 0 0 0 3.9 3.9l1.1-1.3 2.6.8.2 2a2 2 0 0 1-2 1.7A10 10 0 0 1 6.5 8.5 2 2 0 0 1 8 6.5z"/></svg>01632 960417</span>
      <span class="sep" style="left:312px"></span>
      <span class="contact-item contact-item--mail" style="left:340px"><svg viewBox="0 0 24 24" fill="none" stroke="#cdb65c" stroke-width="1.5"><circle cx="12" cy="12" r="11"/><rect x="6.5" y="8" width="11" height="8" rx="1"/><path d="M6.5 8.5l5.5 4 5.5-4"/></svg>sales@ambercoachline.co.uk</span>
      <span class="sep" style="left:651px"></span>
      <span class="contact-item contact-item--web" style="left:685px"><svg viewBox="0 0 24 24" fill="none" stroke="#cdb65c" stroke-width="1.5"><circle cx="12" cy="12" r="11"/><circle cx="12" cy="12" r="6"/><path d="M6 12h12M12 6c-2.5 3-2.5 9 0 12M12 6c2.5 3 2.5 9 0 12"/></svg>www.ambercoachline.co.uk</span>
    </div>
    <div class="brand" style="top:1398px"><span class="brand__dot"></span><span class="brand__name">Amber Coachline</span></div>
  </section>

</div>
</body>
</html>
```